Business card for medical clinic

I need an upmarket, modern medical/health business card for my clinic

Contact Information for Business Card

name, address, email, qr code

```html
<!DOCTYPE html>
<html lang="en">
<head>
<meta charset="utf-8">
<title>Meridian Care Clinic – Business Card</title>
<link href="https://fonts.googleapis.com/css2?family=Cinzel:wght@400;600&family=Crimson+Text:wght@400&display=swap" rel="stylesheet">
<style>
  :root {
    --backdrop: #2a2b2e;
    --card: #1b202b;
    --card-edge: #232a37;
    --brand-blue: #1f9fe0;
    --deep-blue: #0d6fb0;
    --muted-blue: #2a6a9a;
    --text-light: #e8edf3;
    --text-soft: #c9d2dc;
  }
  * { margin: 0; padding: 0; box-sizing: border-box; }
  html, body { width: 1200px; height: 852px; overflow: hidden; }
  body {
    background: var(--backdrop);
    position: relative;
    font-family: "Crimson Text", Georgia, serif;
  }
  .card {
    position: absolute;
    top: 274px;
    width: 530px;
    height: 303px;
    border-radius: 22px;
    background: linear-gradient(160deg, var(--card-edge), var(--card));
    overflow: hidden;
    box-shadow: 0 10px 30px rgba(0,0,0,.45);
  }
  .card-front { left: 50px; }
  .card-back { left: 620px; }

  /* Front: brand name in place of the mark */
  .front-brand {
    position: absolute;
    inset: 0;
    display: flex;
    align-items: center;
    justify-content: center;
    gap: 16px;
  }
  .brand-dot {
    width: 26px; height: 26px;
    border-radius: 50%;
    background: var(--muted-blue);
  }
  .front-brand .brand-name {
    font-family: "Cinzel", "Times New Roman", serif;
    font-weight: 600;
    font-size: 34px;
    letter-spacing: 1px;
    color: var(--muted-blue);
  }

  /* Back */
  .back-brand {
    position: absolute;
    left: 34px; top: 62px;
    display: flex; align-items: center; gap: 10px;
  }
  .back-brand .brand-dot { width: 18px; height: 18px; background: var(--brand-blue); }
  .back-brand .brand-name {
    font-family: "Cinzel", "Times New Roman", serif;
    font-weight: 600;
    font-size: 20px;
    color: var(--brand-blue);
  }
  .contact-list {
    position: absolute;
    left: 318px; top: 72px;
    list-style: none;
    font-size: 13.5px;
    color: var(--text-soft);
    line-height: 19px;
  }
  .contact-list li { display: flex; align-items: center; gap: 8px; }
  .contact-list svg { width: 10px; height: 10px; fill: var(--brand-blue); flex: none; }
  .contact-list .address { padding-left: 0; margin-top: 4px; font-size: 14.5px; }

  .holder {
    position: absolute;
    left: 30px; top: 222px;
  }
  .holder-name {
    font-family: "Cinzel", "Times New Roman", serif;
    font-size: 20px;
    color: var(--brand-blue);
    line-height: 1;
  }
  .holder-role {
    font-size: 14px;
    color: var(--text-light);
    margin-top: 2px;
  }

  .accent-band { position: absolute; left: 0; bottom: 0; width: 530px; height: 303px; }
  .band-label {
    position: absolute;
    right: 24px; top: 206px;
    font-family: "Cinzel", "Times New Roman", serif;
    font-size: 12px;
    letter-spacing: 2.5px;
    color: #ffffff;
  }
</style>
</head>
<body>

  <section class="card card-front" aria-label="Card front">
    <div class="front-brand">
      <span class="brand-dot"></span>
      <span class="brand-name">MERIDIAN CARE CLINIC</span>
    </div>
  </section>

  <section class="card card-back" aria-label="Card back">
    <svg class="accent-band" viewBox="0 0 530 303" aria-hidden="true">
      <defs>
        <linearGradient id="bandFill" x1="0" y1="0" x2="1" y2="0">
          <stop offset="0" stop-color="#0b5f98"/>
          <stop offset="1" stop-color="#2bb3f0"/>
        </linearGradient>
      </defs>
      <path d="M0 294 L330 294 L342 198 L530 180 L530 303 L0 303 Z" fill="url(#bandFill)"/>
      <path d="M0 290 L330 290 L342 194 L530 176" fill="none" stroke="#0a3a5c" stroke-width="2" opacity=".7"/>
    </svg>

    <div class="back-brand">
      <span class="brand-dot"></span>
      <span class="brand-name">MERIDIAN CARE CLINIC</span>
    </div>

    <ul class="contact-list">
      <li>
        <svg viewBox="0 0 10 10"><path d="M2 0.5 L3.6 2.6 L2.8 3.6 Q4 6 6.4 7.2 L7.4 6.4 L9.5 8 L8.5 9.5 Q3 9 0.5 1.5 Z"/></svg>
        0555-010-24680
      </li>
      <li>
        <svg viewBox="0 0 10 10"><path d="M0 2 H10 V8.5 H0 Z M0.6 2.4 L5 5.6 L9.4 2.4" stroke="#1b202b" stroke-width=".8"/></svg>
        hello@meridiancare.com
      </li>
      <li>
        <svg viewBox="0 0 10 10"><circle cx="5" cy="5" r="4.6"/><path d="M0.4 5 H9.6 M5 0.4 V9.6 M2 2.2 Q5 4 8 2.2 M2 7.8 Q5 6 8 7.8" stroke="#1b202b" stroke-width=".7" fill="none"/></svg>
        www.meridiancare.com
      </li>
      <li class="address">48 Elm Row, Brookfield, US 60513</li>
    </ul>

    <div class="holder">
      <p class="holder-name">DANIEL HALE</p>
      <p class="holder-role">Managing Director</p>
    </div>

    <p class="band-label">MERIDIAN CARE CLINIC</p>
  </section>

</body>
</html>
```